New Webpage for High Class Expert Witness Services Company

We are looking for a minimalist design for a webpage that just has our logo and an entry form offer to connect with one of our Liaisons.
The entry form should just ask for Name, Email, Contact Info and Description of Project.

Company Name is: The Marlowe Crest Advisory Services

Number of Pages Required

1 page

```html
<!DOCTYPE html>
<html lang="en">
<head>
<meta charset="utf-8">
<title>Marlowe Crest Advisory Services</title>
<link rel="stylesheet" href="https://fonts.googleapis.com/css2?family=Cinzel:wght@400;500&family=Tinos:wght@400;700&family=Poppins:wght@300;400;500;600&display=swap">
<style>
:root{
  --ink:#111111;
  --hero-dark:#1c1c1e;
  --hero-mid:#3a3a3c;
  --white:#ffffff;
  --muted:#5f5f63;
  --field:#8f9096;
  --field-border:#d8d8dc;
  --card-top:#a2a3a8;
  --card-bottom:#2a2d36;
  --block-grey:#9a9a9f;
  --footer:#121212;
  --footer-text:#d9d9d9;
}
*{box-sizing:border-box;margin:0;padding:0}
html,body{width:980px;height:1200px;overflow:hidden;background:var(--white)}
body{position:relative;font-family:'Poppins',sans-serif;color:var(--ink)}

.hero{position:absolute;left:0;top:0;width:980px;height:490px;overflow:hidden}
.hero-photo{position:absolute;inset:0;background:
  radial-gradient(ellipse at 30% 40%,#4a4a4c 0%,transparent 55%),
  radial-gradient(ellipse at 85% 60%,#3d3d40 0%,transparent 50%),
  linear-gradient(180deg,var(--hero-dark) 0%,var(--hero-mid) 60%,#2a2a2b 100%)}
.site-header{position:absolute;left:0;top:0;width:980px;height:81px;border-bottom:1px solid rgba(255,255,255,.18);display:flex;align-items:center;justify-content:center;gap:10px}
.brand-mark{width:12px;height:12px;background:#d0d0d0}
.brand-name{font-family:'Cinzel',serif;font-weight:400;font-size:20px;letter-spacing:1px;color:#d0d0d0}

.hero-title{position:absolute;left:88px;top:184px;font-family:'Cinzel',serif;color:var(--white);font-weight:400;text-shadow:0 3px 8px rgba(0,0,0,.6)}
.hero-title .line1{display:block;font-size:40px;line-height:48px}
.hero-title .line2{display:block;font-size:28px;line-height:40px}
.hero-sub{position:absolute;left:90px;top:282px;width:340px;font-size:12.6px;line-height:21px;color:var(--white);font-weight:500}
.btn-light{position:absolute;left:91px;top:336px;width:189px;height:42px;background:var(--white);border-radius:5px;display:flex;align-items:center;justify-content:center;font-weight:600;font-size:12px;color:var(--ink);box-shadow:0 2px 6px rgba(0,0,0,.3)}
.slider-dots{position:absolute;left:33px;top:265px;display:flex;flex-direction:column;gap:5px}
.slider-dots span{width:7px;height:7px;border-radius:50%;background:#777}
.slider-dots span.active{background:var(--white);box-shadow:0 0 0 1px #999}

.liaison-card{position:absolute;left:542px;top:139px;width:346px;height:292px;border:1.5px solid var(--field-border);border-radius:13px;background:linear-gradient(180deg,var(--card-top) 0%,#7d7e85 60%,var(--card-bottom) 100%);box-shadow:0 6px 18px rgba(0,0,0,.4)}
.card-title{position:absolute;left:0;top:16px;width:100%;text-align:center;font-family:'Tinos',serif;font-weight:700;font-size:18px;line-height:21px;color:var(--ink)}
.field{position:absolute;height:36px;border:1px solid var(--field-border);border-radius:6px;background:linear-gradient(180deg,#a9aab0,#8e8f96);font-size:10.5px;color:var(--ink);padding:10px 11px;font-weight:500}
.field svg{position:absolute;right:10px;top:12px;width:10px;height:10px;fill:#555}
.f-name{left:11px;top:69px;width:158px}
.f-email{left:175px;top:69px;width:158px}
.f-contact{left:11px;top:111px;width:323px}
.f-desc{left:11px;top:153px;width:323px;height:69px}
.btn-submit{position:absolute;left:11px;top:230px;width:323px;height:42px;background:var(--white);border-radius:5px;display:flex;align-items:center;justify-content:center;font-weight:600;font-size:12px}

.about-backdrop{position:absolute;left:78px;top:560px;width:236px;height:139px;background:var(--block-grey)}
.about-photo{position:absolute;left:91px;top:573px;width:333px;height:347px;border-radius:7px;background:radial-gradient(circle at 47% 38%,#d8d8d8 0%,#6d6d6d 22%,#262626 50%,#0a0a0a 80%)}
.about-heading{position:absolute;left:489px;top:566px;font-family:'Tinos',serif;font-weight:700;font-size:37px;line-height:42px}
.about-divider{position:absolute;left:489px;top:611px;width:102px;height:14px}
.about-text{position:absolute;left:489px;width:399px;font-size:12.6px;line-height:21px;font-weight:300;color:var(--muted);text-align:justify}
.p1{top:637px}.p2{top:742px}
.btn-grey{position:absolute;left:490px;top:879px;width:104px;height:42px;border-radius:5px;background:linear-gradient(180deg,#d4d4d8,#8d8e94);display:flex;align-items:center;justify-content:center;font-weight:600;font-size:12px}

.site-footer{position:absolute;left:0;top:993px;width:980px;height:207px;background:var(--footer)}
.footer-shape{position:absolute;left:70px;top:0;width:260px;height:207px;background:linear-gradient(160deg,#2a2a2a,#171717);clip-path:polygon(0 30%,70% 0,70% 100%,0 100%)}
.footer-brand{position:absolute;left:158px;top:54px;display:flex;align-items:center;gap:9px}
.footer-brand .brand-name{font-size:17px}
.copyright{position:absolute;left:158px;top:122px;font-size:12px;color:var(--footer-text);font-weight:300}
.contact-title{position:absolute;left:593px;top:52px;font-family:'Tinos',serif;font-size:15px;color:var(--white)}
.contact-list{position:absolute;left:591px;top:76px;list-style:none}
.contact-list li{display:flex;align-items:center;gap:4px;height:23px;font-size:12px;color:var(--footer-text);font-weight:300}
.contact-list svg{width:10px;height:10px;fill:#bbb}
</style>
</head>
<body>

<section class="hero">
  <div class="hero-photo" role="img" aria-label="Dark greyscale world map with glowing network lines and nodes"></div>
  <header class="site-header">
    <span class="brand-mark"></span>
    <span class="brand-name">MARLOWE CREST ADVISORY SERVICES</span>
  </header>

  <div class="slider-dots"><span></span><span class="active"></span><span></span><span></span></div>

  <h1 class="hero-title"><span class="line1">MARLOWE CREST</span><span class="line2">ADVISORY SERVICES</span></h1>
  <p class="hero-sub">Delivering Seamless Medical Expert Integration for High-Stakes Cases</p>
  <a class="btn-light">CONNECT WITH A LIAISON</a>

  <form class="liaison-card">
    <h2 class="card-title">CONNECT WITH A MARLOWE<br>LIAISON</h2>
    <div class="field f-name">Name
      <svg viewBox="0 0 10 10"><circle cx="5" cy="3" r="2.4"/><path d="M1 10c0-3 1.8-4.5 4-4.5S9 7 9 10z"/></svg></div>
    <div class="field f-email">Email
      <svg viewBox="0 0 10 10"><rect x="0" y="2" width="10" height="6.5" rx="1"/><path d="M0.5 2.5l4.5 3 4.5-3" stroke="#aaa" stroke-width=".8" fill="none"/></svg></div>
    <div class="field f-contact">Contact Information
      <svg viewBox="0 0 10 10"><circle cx="5" cy="5" r="5"/><path d="M3.2 2.6l1 1-.6.7c.4.8 1 1.4 1.8 1.8l.7-.6 1 1-.7.8C4.6 7.2 2.8 5.4 2.6 3.3z" fill="#aaa"/></svg></div>
    <div class="field f-desc">Description of Project
      <svg viewBox="0 0 10 10"><path d="M1.5 0h5l2 2v8h-7z"/><path d="M3 4h4M3 5.8h4M3 7.6h2.5" stroke="#aaa" stroke-width=".7"/></svg></div>
    <button type="button" class="btn-submit" style="border:0;font-family:'Poppins',sans-serif">SUBMIT</button>
  </form>
</section>

<section class="about">
  <div class="about-backdrop"></div>
  <div class="about-photo" role="img" aria-label="Hand holding a glowing digital sphere of data above a ring of light"></div>
  <h2 class="about-heading">ABOUT US</h2>
  <svg class="about-divider" viewBox="0 0 102 14"><line x1="0" y1="7" x2="35" y2="7" stroke="#999" stroke-width="1"/><circle cx="51" cy="7" r="6" fill="#b5b5b5"/><line x1="67" y1="7" x2="102" y2="7" stroke="#999" stroke-width="1"/></svg>
  <p class="about-text p1">Lorem ipsum dolor sit amet, consectetur adipiscing elit, sed do eiusmod tempor incididunt ut labore et dolore magna aliqua. Ut enim ad minim veniam, quis nostrud exercitation ullamco laboris nisi ut aliquip ex ea commodo consequat.</p>
  <p class="about-text p2">Duis aute irure dolor in reprehenderit in voluptate velit esse cillum dolore eu fugiat nulla pariatur. Excepteur sint occaecat cupidatat non proident, sunt in culpa qui officia deserunt mollit anim id est laborum. Ut enim ad minima veniam, quis nostrum exercitationem ullam corporis suscipit laboriosam, nisi ut aliquid ex ea commodi consequatur</p>
  <a class="btn-grey">READ MORE</a>
</section>

<footer class="site-footer">
  <div class="footer-shape"></div>
  <div class="footer-brand">
    <span class="brand-mark"></span>
    <span class="brand-name">MARLOWE CREST ADVISORY SERVICES</span>
  </div>
  <p class="copyright">© 2026.Marlowe Crest.All Rights Reserved</p>
  <h3 class="contact-title">CONTACT IN FORMATION</h3>
  <ul class="contact-list">
    <li><svg viewBox="0 0 10 10"><path d="M5 0a3.5 3.5 0 0 1 3.5 3.5C8.5 6 5 10 5 10S1.5 6 1.5 3.5A3.5 3.5 0 0 1 5 0z"/><circle cx="5" cy="3.5" r="1.3" fill="#121212"/></svg>Location: Marlowe Crest, US</li>
    <li><svg viewBox="0 0 10 10"><rect x="0" y="2" width="10" height="6.5" rx="1"/><path d="M0.5 2.5l4.5 3 4.5-3" stroke="#121212" stroke-width=".8" fill="none"/></svg>Email Us: info@marlowecrestas.com</li>
    <li><svg viewBox="0 0 10 10"><path d="M1.6 0.8l2 2-1 1.2c.7 1.5 1.9 2.7 3.4 3.4l1.2-1 2 2-1.3 1.4C4 9.5.5 6 .3 2.1z"/></svg>Call Us: +1 555 014 2290</li>
  </ul>
</footer>

</body>
</html>
```